Redesign of business card for Cedar Ridge Mechanical

We are looking for a new design for our business cards for Cedar Ridge Mechanical. We are a plumbing & HVAC construction company, operating on the West Coast of Canada and USA. Logo attached.
Industry/Entity Type
Construction - Plumbing & HVAC
Contact Information for Business Card
Name, address, phone numbers, email, website address
Look and feel
Each slider illustrates characteristics of the customer's brand and the style your logo design should communicate.

```html
<!DOCTYPE html>
<html lang="en">
<head>
<meta charset="utf-8">
<title>Cedar Ridge Mechanical — Business Card</title>
<link rel="stylesheet" href="https://fonts.googleapis.com/css2?family=Arimo:wght@400;700&display=swap">
<style>
  :root {
    --backdrop: #9c9c9c;
    --card-light: #fbfbfb;
    --card-dark: #2e2e2e;
    --ink: #1a1a1a;
    --ink-muted: #8a8a8a;
    --rule: #b8b8b8;
    --reverse: #ffffff;
  }
  * { box-sizing: border-box; margin: 0; padding: 0; }
  html, body {
    width: 1200px;
    height: 1050px;
    overflow: hidden;
    background: var(--backdrop);
    font-family: "Arimo", Arial, sans-serif;
  }
  .canvas {
    position: relative;
    width: 1200px;
    height: 1050px;
  }
  .card {
    position: absolute;
    left: 250px;
    width: 700px;
    height: 400px;
    border-radius: 22px;
    box-shadow: 0 10px 30px rgba(0,0,0,0.22);
  }
  .card--front {
    top: 85px;
    background: var(--card-light);
    color: var(--ink);
  }
  .card--back {
    top: 565px;
    background: var(--card-dark);
    color: var(--reverse);
  }

  /* front */
  .wordmark {
    position: absolute;
    display: flex;
    align-items: center;
    gap: 12px;
    font-weight: 700;
    white-space: nowrap;
  }
  .card--front .wordmark {
    top: 72px;
    right: 58px;
    font-size: 20px;
    color: var(--ink);
  }
  .wordmark__square {
    display: block;
    width: 18px;
    height: 18px;
    background: currentColor;
  }
  .contact-person {
    position: absolute;
    left: 58px;
    top: 175px;
  }
  .contact-person__name {
    font-size: 27px;
    font-weight: 700;
    letter-spacing: -0.3px;
    line-height: 1.05;
  }
  .contact-person__title {
    font-size: 17px;
    color: var(--ink-muted);
    line-height: 1.3;
  }
  .contact-person__phone {
    font-size: 17px;
    line-height: 1.5;
  }
  .contact-address {
    position: absolute;
    left: 58px;
    top: 282px;
    font-size: 17px;
    line-height: 1.3;
    font-style: normal;
  }
  .contact-divider {
    position: absolute;
    left: 312px;
    top: 286px;
    width: 1px;
    height: 52px;
    background: var(--rule);
  }
  .contact-online {
    position: absolute;
    left: 332px;
    top: 286px;
    font-size: 17px;
    line-height: 1.35;
  }

  /* back */
  .card--back .wordmark {
    top: 145px;
    left: 0;
    right: 0;
    justify-content: center;
    font-size: 40px;
    gap: 20px;
    color: var(--reverse);
  }
  .card--back .wordmark__square {
    width: 34px;
    height: 34px;
  }
  .back-web {
    position: absolute;
    left: 0;
    right: 0;
    bottom: 58px;
    text-align: center;
    font-size: 18px;
    letter-spacing: 0.3px;
  }
</style>
</head>
<body>
<main class="canvas">
  <section class="card card--front" aria-label="Business card front">
    <div class="wordmark"><span class="wordmark__square"></span>Cedar Ridge Mechanical</div>

    <div class="contact-person">
      <p class="contact-person__name">Daniel Moreau</p>
      <p class="contact-person__title">President</p>
      <p class="contact-person__phone">(604) 555-0187</p>
    </div>

    <address class="contact-address">
      1427 Harbourview Road<br>
      Port Moody, BC V3H 2K9
    </address>

    <span class="contact-divider"></span>

    <div class="contact-online">
      <p>name@cedarridgemechanical.com</p>
      <p>www.cedarridgemechanical.com</p>
    </div>
  </section>

  <section class="card card--back" aria-label="Business card back">
    <div class="wordmark"><span class="wordmark__square"></span>Cedar Ridge Mechanical</div>
    <p class="back-web">www.cedarridgemechanical.com</p>
  </section>
</main>
</body>
</html>
```